TWPC Business Card Design

Business card for sole operator professional civil and traffic engineer.
Clients are developers and planners who require assistance with traffic strategic master planning advice and design development for access and infrastructure associated with the development.
Colours already in use are greens for the business name and black for other legend. The attached file shows the letterhead template which is currently in use.
Target Market(s)
Professional Clients in development industry
Most clients known to the Principal and card is mostly required to allow ongoing contact
Industry/Entity Type
Business
Contact Information for Business Card
LACHLAN PETTIGREW CONSULTING PARTNERS
ABN 37 814 529 106
PO Box 418 KELWOOD NSW 2619
Lachlan Pettigrew 0412 358 971
l.pettigrew@corvanmail.net

```html
<!DOCTYPE html>
<html lang="en">
<head>
<meta charset="utf-8">
<title>TWPC Business Card</title>
<link rel="stylesheet" href="https://fonts.googleapis.com/css2?family=Arimo:wght@400;700&display=swap">
<style>
  :root {
    --page: #e4e4e2;
    --card: #ffffff;
    --card-shade: #ececec;
    --green: #8cc63f;
    --ink: #111111;
  }
  * { box-sizing: border-box; margin: 0; padding: 0; }
  html, body {
    width: 1200px; height: 848px; overflow: hidden;
    background: var(--page);
    font-family: "Arimo", Arial, sans-serif;
    color: var(--ink);
  }
  .sheet {
    width: 1200px; height: 848px;
    display: flex; flex-direction: column; align-items: center; justify-content: center;
    gap: 40px;
  }
  .card {
    position: relative;
    width: 640px; height: 366px;
    border-radius: 22px;
    background: var(--card);
    box-shadow: 0 6px 18px rgba(0,0,0,.12);
    overflow: hidden;
  }
  .card--back {
    background: linear-gradient(180deg, var(--card) 0%, var(--card-shade) 100%);
  }
  .card__band {
    position: absolute; top: 0; bottom: 0; left: 22px; width: 18px;
    background: var(--green);
  }
  .card__title {
    position: absolute; top: 30px; left: 62px; right: 28px;
    color: var(--green);
    font-size: 23px; letter-spacing: .3px; text-transform: uppercase;
    white-space: nowrap;
  }
  .card--front .card__title { font-size: 21.5px; }
  .card__person {
    position: absolute; top: 120px; right: 36px; text-align: right;
  }
  .card--back .card__person { top: 36px; }
  .card--back .card__title { top: 84px; }
  .card__name {
    font-size: 19px; font-weight: 700; text-transform: uppercase; letter-spacing: .2px;
  }
  .card__abn { font-size: 17px; margin-top: 6px; }
  .contacts {
    position: absolute; left: 68px; bottom: 36px;
    list-style: none;
  }
  .contacts li {
    display: flex; align-items: center; gap: 14px;
    font-size: 18px; line-height: 31px;
  }
  .contacts svg { width: 18px; height: 18px; flex: none; fill: var(--ink); }
  .contacts .addr { text-transform: uppercase; }
</style>
</head>
<body>
<main class="sheet">

  <section class="card card--front">
    <div class="card__band"></div>
    <h1 class="card__title">Lachlan Pettigrew Consulting Partners</h1>
    <div class="card__person">
      <p class="card__name">Lachlan Pettigrew</p>
      <p class="card__abn">ABN 37 814 529 106</p>
    </div>
    <ul class="contacts">
      <li><svg viewBox="0 0 24 24" aria-hidden="true"><path d="M2 8c0-3 4-5 10-5s10 2 10 5v2h-5V8c-1-1-3-1.5-5-1.5S8 7 7 8v2H2z"/><path d="M6 11h12l3 10H3z"/></svg>0412 358 971</li>
      <li><svg viewBox="0 0 24 24" aria-hidden="true"><path d="M2 5h20v14H2z M4 7v1l8 6 8-6V7l-8 5z" fill-rule="evenodd"/></svg>l.pettigrew@corvanmail.net</li>
      <li><svg viewBox="0 0 24 24" aria-hidden="true"><path d="M12 1a7 7 0 0 0-7 7c0 6 7 15 7 15s7-9 7-15a7 7 0 0 0-7-7zm0 4a3 3 0 1 1 0 6 3 3 0 0 1 0-6z" fill-rule="evenodd"/></svg><span class="addr">418 Kelwood NSW 2619</span></li>
    </ul>
  </section>

  <section class="card card--back">
    <div class="card__band"></div>
    <h2 class="card__title">Lachlan Pettigrew</h2>
    <div class="card__person">
      <p class="card__name">Lachlan Pettigrew</p>
      <p class="card__abn">ABN 37 814 529 106</p>
    </div>
    <ul class="contacts">
      <li><svg viewBox="0 0 24 24" aria-hidden="true"><path d="M2 8c0-3 4-5 10-5s10 2 10 5v2h-5V8c-1-1-3-1.5-5-1.5S8 7 7 8v2H2z"/><path d="M6 11h12l3 10H3z"/></svg>0412 358 971</li>
      <li><svg viewBox="0 0 24 24" aria-hidden="true"><path d="M2 5h20v14H2z M4 7v1l8 6 8-6V7l-8 5z" fill-rule="evenodd"/></svg>l.pettigrew@corvanmail.net</li>
      <li><svg viewBox="0 0 24 24" aria-hidden="true"><path d="M12 1a7 7 0 0 0-7 7c0 6 7 15 7 15s7-9 7-15a7 7 0 0 0-7-7zm0 4a3 3 0 1 1 0 6 3 3 0 0 1 0-6z" fill-rule="evenodd"/></svg><span class="addr">418 Kelwood NSW 2619</span></li>
    </ul>
  </section>

</main>
</body>
</html>
```